Business Card Design for Occupational Medicine Start Up Company

We need to design a professional business card. We are a healthcare company providing occupational medicine services to blue collar industries. We are professional, efficient and high quality service providers.

Target Market(s)

Blue Collar Industry: Shipbuilding, Ports, Trucking Companies; The Executives and Safety Officers for these companies

Industry/Entity Type

Healthcare

Contact Information for Business Card

Logo, Name, Title, Email, Phone

Other font styles liked:
• Please match our Brand Guide

Requirements
Must have
• Our Company Colors and Logo

```html
<!DOCTYPE html>
<html lang="en">
<head>
<meta charset="utf-8">
<title>CrewWell Clinics – Business Card</title>
<link rel="stylesheet" href="https://fonts.googleapis.com/css2?family=Poppins:wght@400;600;700&display=swap">
<style>
  :root{
    --navy:#1e2465;
    --brand-blue:#2a2f87;
    --sky:#22a6df;
    --amber:#f7b24a;
    --paper:#ffffff;
    --ink:#1a1a1a;
    --rule:#9a9a9a;
    --backdrop:#a3a3a3;
  }
  *{margin:0;padding:0;box-sizing:border-box}
  html,body{width:1200px;height:1200px;overflow:hidden}
  body{background:var(--backdrop);font-family:"Poppins",sans-serif;position:relative}
  .card{position:absolute;top:303px;width:368px;height:594px}
  .card-back{left:200px;background:var(--navy);color:var(--paper)}
  .card-front{left:599px;width:364px;background:var(--paper);color:var(--ink);text-align:center}

  .back-emblem{position:absolute;left:50%;top:290px;transform:translate(-50%,-50%);
    display:flex;flex-direction:column;align-items:center;gap:18px}
  .back-emblem .dot{width:150px;height:150px;border-radius:50%;background:var(--brand-blue)}
  .back-emblem .name{font-weight:600;font-size:24px;letter-spacing:2px;color:var(--paper)}
  .back-url{position:absolute;left:0;right:0;top:530px;text-align:center;font-size:16px;letter-spacing:2px}

  .brand{position:absolute;left:0;right:0;top:88px;display:flex;flex-direction:column;align-items:center}
  .brand .dot{width:70px;height:70px;border-radius:50%;background:var(--sky)}
  .brand .name{margin-top:22px;font-weight:600;font-size:30px;line-height:1;color:var(--brand-blue);letter-spacing:1px}
  .brand .sub{margin-top:8px;font-weight:600;font-size:18px;line-height:1;letter-spacing:7px;color:var(--brand-blue)}

  .person{position:absolute;left:0;right:0;top:334px}
  .person .full-name{font-weight:700;font-size:25px;line-height:1.05;color:var(--brand-blue)}
  .person .role{font-size:15px;line-height:1.2}

  .icon-row{position:absolute;left:87px;right:87px;top:395px;display:flex;align-items:center;justify-content:center;gap:4px}
  .icon-row .rule{flex:1;height:1px;background:var(--rule)}
  .icon-row .rule:first-child{margin-right:4px}
  .icon-row .rule:last-child{margin-left:4px}
  .icon{width:25px;height:25px;border-radius:3px;background:var(--brand-blue);display:flex;align-items:center;justify-content:center}

  .contact{position:absolute;left:0;right:0;top:426px;font-size:16px;line-height:21px}
  .divider{position:absolute;left:88px;right:81px;top:507px;height:1px;background:var(--rule)}
  .address{position:absolute;left:0;right:0;top:519px;font-size:16px;line-height:21px}
</style>
</head>
<body>
  <section class="card card-back">
    <div class="back-emblem">
      <span class="dot"></span>
      <span class="name">CREWWELL</span>
    </div>
    <p class="back-url">www.crewwellclinics.com</p>
  </section>

  <section class="card card-front">
    <div class="brand">
      <span class="dot"></span>
      <span class="name">CREWWELL</span>
      <span class="sub">CLINICS</span>
    </div>

    <div class="person">
      <h1 class="full-name">DANIEL HARPER</h1>
      <p class="role">Managing Director</p>
    </div>

    <div class="icon-row">
      <span class="rule"></span>
      <span class="icon" aria-label="Phone">
        <svg width="16" height="16" viewBox="0 0 16 16"><path d="M3 2h3l1 3-2 1a8 8 0 0 0 5 5l1-2 3 1v3a1 1 0 0 1-1 1A12 12 0 0 1 2 3a1 1 0 0 1 1-1z" fill="#fff"/></svg>
      </span>
      <span class="icon" aria-label="Email">
        <svg width="16" height="16" viewBox="0 0 16 16"><rect x="1.5" y="3.5" width="13" height="9" fill="none" stroke="#fff" stroke-width="1.3"/><path d="M1.5 3.5l6.5 5 6.5-5" fill="none" stroke="#fff" stroke-width="1.3"/></svg>
      </span>
      <span class="icon" aria-label="Website">
        <svg width="16" height="16" viewBox="0 0 16 16"><circle cx="8" cy="8" r="6.2" fill="none" stroke="#fff" stroke-width="1.3"/><ellipse cx="8" cy="8" rx="2.6" ry="6.2" fill="none" stroke="#fff" stroke-width="1"/><path d="M2 8h12" stroke="#fff" stroke-width="1"/></svg>
      </span>
      <span class="rule"></span>
    </div>

    <div class="contact">
      <p>044-555 010 222</p>
      <p>hello@crewwellclinics.com</p>
      <p>www.crewwellclinics.com</p>
    </div>

    <div class="divider"></div>

    <div class="address">
      <p>87, Harbour Works Road</p>
      <p>90817, Portland Bay</p>
    </div>
  </section>
</body>
</html>
```